New Business Card Design Project LORVANTI-Italy

we are LORVANTI-Italy
our company in the market for 3 years we are luxury cosmetic company and its about time for a facelift :)
i will like to have elegant luxurious and unique business card
that will give the person that get it a unique, luxurious and elegant impression
I'm VERY OPEN FOR NEW IDEAS , even duo i add a few files of things that i see on line and i like them

i add my logo as well
my website is LORVANTI.COM
(if you would like to see the main style that we have)

Target Market(s)

adult that have money :)

Industry/Entity Type

Business

Contact Information for Business Card

Name - Dario Lorvanti
Position - CEO and CO Founder
address - 4817 E Halvern
telephone - 555-384-1926
email - dario@lorvanti.com
fax - 555-384-1926
website - LORVANTI.COM

Colors
000000
959595
fbee3e
ffffff

Requirements
Must have
• big logo in GOLD color
• elegant look
• impressive
Nice to have
• not must but maybe classy pattern background
• not must but maybe emblem
• maybe clear plastic business card
Should not have
• colors
• images

```html
<!DOCTYPE html>
<html lang="en">
<head>
<meta charset="utf-8">
<title>LORVANTI Italy – Business Card</title>
<link rel="stylesheet" href="https://fonts.googleapis.com/css2?family=Cinzel:wght@400&family=Mulish:wght@400&display=swap">
<style>
  :root {
    --page: #0d0c0b;
    --card-top: #201f1d;
    --card-bottom: #141312;
    --gold: #cfa73a;
    --gold-light: #e3c25a;
    --tab: #3b3a39;
    --ink: #1a1917;
    --pattern: rgba(255, 255, 255, 0.05);
  }
  * { box-sizing: border-box; margin: 0; padding: 0; }
  html, body {
    width: 1200px; height: 1200px; overflow: hidden;
    background: var(--page);
  }
  .stage {
    width: 1200px; height: 1200px;
    display: flex; justify-content: center; align-items: center; gap: 60px;
  }
  .card {
    position: relative;
    width: 420px; height: 736px;
    background: linear-gradient(170deg, var(--card-top), var(--card-bottom));
    overflow: hidden;
  }
  .card__pattern {
    position: absolute; left: -140px; bottom: -300px;
    width: 700px; height: 640px; border-radius: 50%;
    background: radial-gradient(circle, var(--pattern) 0%, rgba(255,255,255,0.035) 45%, transparent 70%);
  }
  .brand {
    position: absolute; left: 0; right: 0;
    display: flex; flex-direction: column; align-items: center;
    color: var(--gold);
    font-family: "Cinzel", serif; font-weight: 400;
  }
  .brand__circle {
    border: 3px solid var(--gold); border-radius: 50%;
  }
  /* front */
  .card--front .brand { top: 136px; }
  .card--front .brand__circle { width: 166px; height: 166px; margin-bottom: 42px; }
  .card--front .brand__name { font-size: 60px; letter-spacing: 1px; line-height: 1; }

  /* back */
  .card__stripe {
    position: absolute; left: 0; top: 0; bottom: 0; width: 18px;
    background: var(--gold);
  }
  .card--back .brand { top: 56px; left: 18px; }
  .card--back .brand__circle { width: 106px; height: 106px; margin-bottom: 26px; }
  .card--back .brand__name { font-size: 42px; letter-spacing: 1px; line-height: 1; }

  .contacts { position: absolute; left: 18px; right: 0; top: 306px; list-style: none; }
  .contact {
    position: absolute; right: 0; left: 0; height: 32px;
    display: flex; align-items: center; justify-content: flex-end;
  }
  .contact__text {
    font-family: "Mulish", sans-serif; color: var(--gold);
    font-size: 14px; text-align: right; margin-right: 10px; line-height: 1.15;
  }
  .contact__text--name { font-size: 21px; }
  .contact__text small { display: block; font-size: 13px; }
  .contact__icon {
    width: 30px; height: 30px; background: var(--gold);
    display: flex; align-items: center; justify-content: center;
    flex: none;
  }
  .contact__icon svg { width: 20px; height: 20px; fill: var(--ink); stroke: var(--ink); }
  .contact__tab { width: 48px; height: 32px; background: var(--tab); flex: none; }
</style>
</head>
<body>
<main class="stage">

  <section class="card card--front" aria-label="Card front">
    <div class="card__pattern" role="img" aria-label="Faint circular ornamental pattern on leather texture"></div>
    <div class="brand">
      <div class="brand__circle"></div>
      <div class="brand__name">LORVANTI</div>
    </div>
  </section>

  <section class="card card--back" aria-label="Card back">
    <div class="card__pattern" role="img" aria-label="Faint circular ornamental pattern on leather texture"></div>
    <div class="card__stripe"></div>
    <div class="brand">
      <div class="brand__circle"></div>
      <div class="brand__name">LORVANTI</div>
    </div>

    <ul class="contacts">
      <li class="contact" style="top:0">
        <span class="contact__text contact__text--name">Dario Lorvanti<small>CEO and CO Founder</small></span>
        <span class="contact__icon"><svg viewBox="0 0 24 24"><circle cx="12" cy="8" r="4.5"/><path d="M3 22c0-5 4-8 9-8s9 3 9 8z"/></svg></span>
        <span class="contact__tab"></span>
      </li>
      <li class="contact" style="top:72px">
        <span class="contact__text">4817 E Halvern</span>
        <span class="contact__icon"><svg viewBox="0 0 24 24"><path d="M12 2a7 7 0 0 0-7 7c0 5 7 13 7 13s7-8 7-13a7 7 0 0 0-7-7zm0 10a3 3 0 1 1 0-6 3 3 0 0 1 0 6z"/></svg></span>
        <span class="contact__tab"></span>
      </li>
      <li class="contact" style="top:134px">
        <span class="contact__text">555-384-1926</span>
        <span class="contact__icon"><svg viewBox="0 0 24 24"><path d="M6.6 10.8a15 15 0 0 0 6.6 6.6l2.2-2.2c.3-.3.7-.4 1-.2 1.1.4 2.3.6 3.6.6.6 0 1 .4 1 1V20c0 .6-.4 1-1 1A17 17 0 0 1 3 4c0-.6.4-1 1-1h3.5c.6 0 1 .4 1 1 0 1.3.2 2.5.6 3.6.1.3 0 .7-.2 1z"/></svg></span>
        <span class="contact__tab"></span>
      </li>
      <li class="contact" style="top:195px">
        <span class="contact__text">dario@lorvanti.com</span>
        <span class="contact__icon"><svg viewBox="0 0 24 24"><path d="M2 5h20v14H2z" fill="none" stroke-width="2"/><path d="M2 5l10 8 10-8" fill="none" stroke-width="2"/></svg></span>
        <span class="contact__tab"></span>
      </li>
      <li class="contact" style="top:258px">
        <span class="contact__text">555-384-1926</span>
        <span class="contact__icon"><svg viewBox="0 0 24 24"><path d="M7 3h10v5H7z"/><path d="M3 9h18v8h-3v4H6v-4H3z"/><path d="M8 15h8v4H8z" fill="#cfa73a" stroke="none"/></svg></span>
        <span class="contact__tab"></span>
      </li>
      <li class="contact" style="top:322px">
        <span class="contact__text">LORVANTI.COM</span>
        <span class="contact__icon"><svg viewBox="0 0 24 24" fill="none" stroke-width="1.8"><circle cx="12" cy="12" r="9" fill="none"/><path d="M3 12h18M12 3c3 3 3 15 0 18M12 3c-3 3-3 15 0 18" fill="none"/></svg></span>
        <span class="contact__tab"></span>
      </li>
    </ul>
  </section>

</main>
</body>
</html>
```